Business Card design for insurance broker in Denver, CO, USA

I need a business card designed using this logo that was just created. We sell life and disability income insurance to US consumers.
Looking for a professionally designed card to make use of the logo and have something to hand to prospects or new business referral sources. The card could be white, gray, black or whatever you would recommend.

Target Market(s)

US Consumers and other financial professionals that I partner with.

Industry/Entity Type

Insurance Broker

Contact Information for Business Card

Owen T. Farrow, CLU, LUTCF (please note that CLU should have a superscript R in a circle for registered trademark)
President
phone (303) 555-0187
email owen@keelbrookcover.example
4620 W. Halvern Rd, Suite 300, Greenwood Village, CO 80111
Somewhere fit in a tagline saying "Your resource for life, long term care, and disability insurance" (maybe the back if it doesn't fit on the front, your call)

Font styles to use
Sans Serif

Requirements
Must have
• Must have logo in correct blue and gray colors, my name, address, phone, email. Order and placement determined by the designer.
• I just want something that looks a more professional than what I could have done using the business card designer tool on pixelbazaar.example or QuillPress, or any other do-it-yourself tool
• A regular rectangular business card with square corners is preferred
Nice to have
• I included the logos of 2 organizations I belong to (GKLS and WOBCE). They should be small, but visible on the back only. If it doesn’t look good, this is not a requirement, feel free to drop it.
Should not have
• Do not add any colors not already in the logo, except use of black and whites which are okay. If you use the logo on the back and want to make that in all black, gray or white, that may be okay as well.

```html
<!DOCTYPE html>
<html lang="en">
<head>
<meta charset="utf-8">
<title>Keelbrook Cover – Business Card</title>
<link href="https://fonts.googleapis.com/css2?family=Lato:wght@400;700&display=swap" rel="stylesheet">
<style>
  :root {
    --backdrop: #1b1b1c;
    --card: #232324;
    --blue: #2a8ad6;
    --gray: #b9babc;
    --badge: #5a5c60;
    --white: #f2f2f2;
  }
  html, body {
    margin: 0;
    width: 1200px;
    height: 900px;
    overflow: hidden;
    background: var(--backdrop);
    font-family: "Lato", Arial, sans-serif;
  }
  .canvas {
    position: relative;
    width: 1200px;
    height: 900px;
  }
  .card {
    position: absolute;
    left: 250px;
    width: 700px;
    height: 400px;
    background: var(--card);
    border-bottom: 6px solid var(--blue);
    box-sizing: border-box;
    box-shadow: 0 12px 30px rgba(0,0,0,.45);
  }
  .card--front { top: 30px; }
  .card--back { top: 464px; }

  .brand {
    display: flex;
    align-items: center;
    gap: 14px;
    color: var(--blue);
    font-weight: 700;
    letter-spacing: .02em;
  }
  .brand__mark {
    border: 4px solid var(--blue);
    border-radius: 50%;
    box-sizing: border-box;
    flex: none;
  }

  .card--front .brand {
    position: absolute;
    left: 0; right: 0;
    top: 150px;
    justify-content: center;
    font-size: 46px;
  }
  .card--front .brand__mark { width: 70px; height: 70px; }
  .tagline {
    position: absolute;
    left: 0; right: 0;
    bottom: 26px;
    margin: 0;
    text-align: center;
    color: var(--white);
    font-size: 14px;
    letter-spacing: .04em;
    text-transform: uppercase;
  }

  .card--back .brand {
    position: absolute;
    left: 50px;
    top: 150px;
    font-size: 30px;
    line-height: 1.05;
  }
  .card--back .brand__mark { width: 56px; height: 56px; border-width: 3px; }
  .divider {
    position: absolute;
    left: 340px;
    top: 104px;
    width: 2px;
    height: 170px;
    background: var(--blue);
  }
  .contact {
    position: absolute;
    left: 366px;
    top: 100px;
    color: var(--white);
    font-size: 17px;
    line-height: 1.3;
  }
  .contact__name {
    color: var(--blue);
    font-size: 22px;
    font-weight: 700;
  }
  .contact__name sup { font-size: 10px; }
  .contact__title { margin-bottom: 12px; }
  .contact__address { margin-bottom: 10px; }
  .contact__line {
    display: flex;
    align-items: center;
    gap: 8px;
  }
  .contact__line svg { width: 14px; height: 14px; flex: none; }
  .badges {
    position: absolute;
    left: 410px;
    top: 305px;
    display: flex;
    gap: 30px;
    align-items: center;
  }
  .badge { background: var(--badge); }
  .badge--square { width: 56px; height: 56px; }
  .badge--round { width: 56px; height: 56px; border-radius: 50%; }
</style>
</head>
<body>
<main class="canvas">
  <section class="card card--front">
    <div class="brand">
      <span class="brand__mark"></span>
      <span class="brand__name">Keelbrook Cover</span>
    </div>
    <p class="tagline">Your resource for life, long term care, and disability insurance</p>
  </section>

  <section class="card card--back">
    <div class="brand">
      <span class="brand__mark"></span>
      <span class="brand__name">Keelbrook<br>Cover</span>
    </div>
    <div class="divider"></div>
    <div class="contact">
      <div class="contact__name">Owen T. Farrow, CLU<sup>®</sup>, LUTCF</div>
      <div class="contact__title">President</div>
      <div class="contact__address">4620 W. Halvern Rd, Suite 300,<br>Greenwood Village, CO 80111</div>
      <div class="contact__line">
        <svg viewBox="0 0 24 24" aria-hidden="true"><path fill="#2a8ad6" d="M6.6 10.8a15 15 0 0 0 6.6 6.6l2.2-2.2c.3-.3.7-.4 1-.2 1.1.4 2.300.6 3.6.6.6 0 1 .4 1 1V20c0 .6-.4 1-1 1A17 17 0 0 1 3 4c0-.6.4-1 1-1h3.5c.6 0 1 .4 1 1 0 1.3.2 2.5.6 3.6.1.3 0 .7-.2 1z"/></svg>
        <span>(303) 555-0187</span>
      </div>
      <div class="contact__line">
        <svg viewBox="0 0 24 24" aria-hidden="true"><rect x="3" y="6" width="18" height="12" fill="none" stroke="#2a8ad6" stroke-width="2"/><path d="M3 6l9 7 9-7" fill="none" stroke="#2a8ad6" stroke-width="2"/></svg>
        <span>owen@keelbrookcover.example</span>
      </div>
    </div>
    <div class="badges">
      <div class="badge badge--square" role="img" aria-label="WOBCE membership badge"></div>
      <div class="badge badge--round" role="img" aria-label="GKLS membership badge"></div>
    </div>
  </section>
</main>
</body>
</html>
```